Updated VOLU Brochure for cultural event

We are seeking an updated brochure in a standard 8.5 by 11 size, and we have provided the current brochure and necessary information for inclusion. We desire a fresh new design that conveys a modern and elegant aesthetic. As we anticipate making changes to the brochure periodically, we require an editable program for its creation. Our First Nation Community values our beliefs and appearance, and we hope the brochure will reflect our welcoming nature while standing out from the crowd.
Attached Brochure is from last year
Wants and needs:
Page one. A redesign All the info on the page needs to be there but it needs a face lift.
Page two. Information is attached for that but do need this page editable for future. Join us for an immersive cultural experience at Pell Creek First Nation (PCFN) community, located in Northeastern BC. We invite you to participate in the Volu Camping Experience, a unique opportunity to forge relationships with our community, connect with our Chief and Council, and engage with industry leaders. Your participation in this grassroots event will earn your company credibility for the work it performs in PCFN territory.

Through this experience, you'll gain an appreciation and understanding of our community and cultural values, while meeting with key office staff, industry C-Suite level executives, industry Indigenous relations staff, and local, regional, and provincial representatives in a positive and welcoming space. The recent Tanwick V. British Columbia 2021 decision has significantly shifted how consultation and engagement will be managed on our lands. To help you better understand why managing cumulative effects is essential to PCFN, we welcome you to join us for a three-day camping experience from May 23 to May 26, 2023.

The Volu Camping Experience offers a variety of activities, including a dinner visit to NAH 'B'lo, the 12,500-year-old cave, where an archeological dig is currently underway, accompanied by our economic development corporation team from Faret Development LP. The event also includes traditional bush camping in elegant teepees/wall tents, dry meat making, and participation in our Pell Day, a 30+ year cultural education and anti-racism event held on May 25, 2023. During Pell Day, over 400+ students from School District #47 participate in traditional activities, including moose hide preparation, beaver skinning, archaeology dig, dry-meat making, trapping demonstrations, Bannock on a stick, storytelling, drumming, and tea dance around the campfire to the beat of our drums.

Root yourself to the land, connect with your inner self, and be transformed alongside other important dignitaries as you partake in these multi-sensory experiences on our cultural grounds. This is our second combined camping/Pell Day experience, and we hope to continue and build on it for future cultural tourism activities such as guided bush camps, hikes, and hunts.

If you are unable to join us for the full three-day camping experience, we encourage you to join us for the one-day Pell Day event, along with other important decision-makers and political leaders. We have a helicopter landing area close to the activities for your convenience. Please RSVP to Owen Marsh, Nahm? B'lo Cultural Productions Manager at OwenMarsh@pellcreekfn.example or Dale Finch, PCFN Councilor at Dfinch@pellcreekfn.example. We are looking forward to hosting you!

Page 3 - Signatures Names can be put in but I will need to add signatures after.
Page 4. 2023 Sponsors this will need to be editable as we get new ones in.
Page 5. Participant supplies check list. All of this is good just need to make it look better
Page 6. Agenda Dates need to change May 23-26 2023 This page also needs to be editable .. the days Dates need to change also.
Page 7 . Same info can be there.
All pages can use different photos where you need them..
Different logos on the sponsor page so that needs to be editable.
Daily Agenda needs to be editable .. definitely a better table

Things that need to be editable are dates (May 23-26th 2023)

I am just gathering some more photos for the brochure and will add them as I go .

Target Market(s)

Corporate partners

Colors
0054AA
0677BA
7BADD7
CADEEF
E8F1F8
0094D4
00A9DD
6FCCEA
C7EBF8
E9F6FB
00AB8E
00BBA5
67D7C9
C6EFE9
E9F9F6
59FF00
82FF00
B8FF75
E3FFCB
F4FFEA
FFF300
FFF600
FEFA6F
FFFEC7
FFFEE8
FFC000
F8CF3A
FAE287
FDF2CF
FEFAEE
F0912C
F2A743
F7CA91
FBE8D2
FDF5EE
EE7325
F08F49
F5BC92
FAE3D3
FDF4ED
EB3D1F
EC4F4E
F09395
F8D3D4
FCEDEE

Requirements
Must have
• The information that was provided
Nice to have
• We would like this to be very inviting and professional
Should not have
• cartoons or anything that looks cheap

```html
<!DOCTYPE html>
<html lang="en">
<head>
<meta charset="utf-8">
<title>Volu Executive Camping Experience – Pell Day 2023</title>
<link rel="stylesheet" href="https://fonts.googleapis.com/css2?family=Cinzel:wght@500;700&family=Oswald:wght@500;700&family=Montserrat:wght@400;600;700&display=swap">
<style>
:root{
  --navy:#0054AA;
  --blue:#0677BA;
  --sky:#7BADD7;
  --ink:#1d1d1d;
  --paper:#ffffff;
  --stage:#c4c4c4;
  --line:#0677BA;
  --red:#EB3D1F;
}
*{box-sizing:border-box;margin:0;padding:0}
html,body{width:690px;height:1200px;overflow:hidden}
body{background:var(--stage);position:relative;font-family:"Montserrat",sans-serif;color:var(--ink)}
.page{position:absolute;background:var(--paper);overflow:hidden}
.cover{left:147px;top:41px;width:395px;height:304px}
.inner{width:280px;height:216px}
.p-invite{left:50px;top:404px}
.p-sign{left:360px;top:404px}
.p-sponsors{left:48px;top:668px}
.p-checklist{left:360px;top:668px}
.p-agenda{left:48px;top:925px}
.p-thanks{left:361px;top:925px}
.photo{position:absolute}
.wave{position:absolute;display:block}
.brand{position:absolute;display:flex;align-items:center;gap:2px;font-family:"Cinzel",serif;font-weight:700;color:var(--ink)}
.brand .dot{width:6px;height:6px;border-radius:50%;background:var(--blue)}
.inner .brand{right:12px;top:14px;font-size:8px}
.tab{position:absolute;left:0;background:var(--navy);color:#fff;font-family:"Cinzel",serif;font-weight:700;padding:1px 12px 1px 12px;border-radius:0 10px 0 0;white-space:nowrap}

/* cover */
.cover-photo{left:0;top:0;width:395px;height:250px;background:radial-gradient(circle at 72% 22%,#bfe0ff 0 5%,transparent 6%),linear-gradient(180deg,#06152e 0%,#0d3a72 45%,#1c5fa8 60%,#0a2446 100%)}
.cover-title{position:absolute;left:23px;top:214px;width:190px}
.cover-title .kicker{font-family:"Cinzel",serif;font-weight:500;font-size:15px;line-height:19px;color:#2a2a2a;letter-spacing:.2px;white-space:nowrap}
.cover-title .event{font-family:"Oswald",sans-serif;font-weight:700;font-size:31px;line-height:36px;color:var(--navy);white-space:nowrap}
.cover-partners{position:absolute;left:222px;top:242px;display:flex;align-items:center;gap:8px}
.cover-partners .divider{width:1px;height:52px;background:#333}
.partner{font-family:"Montserrat",sans-serif;font-weight:600;font-size:8px;line-height:10px;color:#222;display:flex;align-items:center;gap:3px;white-space:nowrap}
.partner .dot{width:8px;height:8px;border-radius:50%;background:var(--blue);flex:none}

/* invite */
.invite-body{position:absolute;left:11px;top:44px;width:266px;font-size:3.25px;line-height:4.9px;color:#333}
.invite-body p{margin-bottom:2.4px;text-align:justify}
.float-spacer{float:right;width:0;height:35px}
.invite-photo{float:right;clear:right;width:62px;height:62px;margin:0 10px 2px 4px;border-radius:50%;shape-outside:circle(50%);background:linear-gradient(180deg,#7f6fb5 0%,#f4c24a 42%,#f6a531 48%,#6e9a3a 55%,#3f6a25 100%)}
.signoff{position:absolute;right:14px;bottom:8px;font-family:"Oswald",sans-serif;font-weight:500;font-size:7px;color:var(--navy)}

/* signature */
.p-sign .tab{top:46px;font-size:10px}
.sig-list{position:absolute;left:11px;top:58px;width:258px;list-style:none}
.sig-list li{display:flex;justify-content:space-between;align-items:flex-end;height:15.6px;font-size:5.6px;font-weight:600}
.sig-list li span.rule{width:132px;border-bottom:.6px solid #333;height:6px}
.sign-photo{left:0;top:125px;width:280px;height:91px;background:linear-gradient(180deg,#2a2a66 0%,#6b4f9b 40%,#b892c9 62%,#2a3640 80%,#17232a 100%)}

/* sponsors */
.p-sponsors .tab{top:52px;font-size:10px}
.sponsor-grid{position:absolute;left:11px;top:72px;display:grid;grid-template-columns:repeat(4,61px);grid-auto-rows:18px;column-gap:4px;row-gap:6px}
.sponsor{border:.8px solid var(--blue);border-radius:9px;display:flex;align-items:center;justify-content:center;gap:2px;font-family:"Montserrat",sans-serif;font-weight:600;font-size:5.2px;color:#333;text-align:center;line-height:5.6px}
.sponsor .dot{width:4px;height:4px;border-radius:50%;background:var(--blue);flex:none}

/* checklist */
.p-checklist .tab{top:41px;font-size:10px}
.check-intro{position:absolute;left:12px;top:55px;width:260px;font-size:3px;line-height:4.3px;color:#333}
.check-intro b{color:var(--navy)}
.supplies{position:absolute;left:12px;width:266px;border-collapse:collapse;font-size:2.9px;line-height:3.6px}
.supplies td,.supplies th{border:.3px solid var(--line);padding:0 1.5px;text-align:left;font-weight:400}
.supplies th{color:var(--navy);font-weight:600}
.supplies th.have{color:#3aa31a}.supplies th.need{color:var(--red)}
.supplies .group td{color:var(--navy);font-weight:600;text-align:center}
.supplies td:nth-child(1){width:95px}.supplies td:nth-child(2),.supplies td:nth-child(3){width:30px}
.supplies .mark{text-align:center}
.t-own{top:70px}.t-given{top:152px}
.check-foot{position:absolute;left:12px;top:177px;font-size:3px;line-height:4.3px;color:#333}
.check-foot .warn{color:var(--red)}
.check-foot .contact{color:var(--navy);font-weight:600;font-size:4.8px;line-height:7px}

/* agenda */
.p-agenda .tab{top:40px;font-size:7.6px;padding-right:14px}
.agenda-dates{position:absolute;left:11px;top:56px;font-family:"Oswald",sans-serif;font-weight:500;font-size:10px;color:#222}
.agenda-photo{left:208px;top:0;width:72px;height:216px;background:linear-gradient(180deg,#1d2430 0%,#3b2a20 40%,#b4541c 70%,#f2a23a 82%,#221612 100%)}
.day{position:absolute;left:12px;width:206px;border-collapse:collapse;font-size:2.6px;line-height:3.6px;color:#333}
.day th{font-family:"Montserrat",sans-serif;font-weight:700;font-size:3.9px;color:var(--navy);text-align:left;border-bottom:.5px solid var(--navy);padding-bottom:.5px}
.day td{vertical-align:top;padding-top:1px}
.day td.notes{border-left:.4px solid #333;padding-left:12px}
.day .c1{width:26px}.day .c2{width:25px}.day .c3{width:84px}
.day .flight{color:var(--navy)}
.d1{top:81px}.d2{top:113px}.d3{top:145px}.d4{top:177px}

/* thanks */
.thanks-photo{left:0;top:0;width:280px;height:160px;background:linear-gradient(180deg,#dfeef8 0%,#b8cfa0 30%,#6f8a4d 45%,#5b5f6c 70%,#3d4556 100%)}
.thanks-text{position:absolute;left:16px;top:159px}
.thanks-text .pre{font-size:6px;letter-spacing:.2px;color:#333}
.thanks-text .greet{font-family:"Montserrat",sans-serif;font-weight:700;font-size:13px;line-height:17px;color:var(--navy)}
.thanks-text .thanks{font-family:"Cinzel",serif;font-weight:700;font-size:15px;line-height:17px;color:#222}
.p-thanks .brand-lg{position:absolute;right:14px;bottom:12px;font-family:"Cinzel",serif;font-weight:700;font-size:15px;color:#222;display:flex;align-items:center;gap:3px}
.brand-lg .dot{width:12px;height:12px;border-radius:50%;background:var(--blue)}
</style>
</head>
<body>

<!-- Cover -->
<section class="page cover">
  <div class="photo cover-photo" role="img" aria-label="Night photograph of a snowy mountain and full moon reflected in a calm lake"></div>
  <svg class="wave" style="left:0;top:0" width="395" height="304" viewBox="0 0 395 304" aria-hidden="true">
    <path d="M0 212 C30 182 55 158 90 155 C145 150 190 198 250 210 C300 219 350 212 395 198 L395 304 L0 304Z" fill="#fff"/>
    <path d="M0 218 C30 180 75 150 130 160 C85 152 45 172 0 206Z" fill="var(--navy)"/>
    <path d="M300 219 C340 216 370 206 395 190 L395 198 C365 212 335 220 300 219Z" fill="var(--blue)"/>
  </svg>
  <div class="cover-title">
    <div class="kicker">Volu Executive<br>Camping Experience</div>
    <div class="event">PELL DAY 2023</div>
  </div>
  <div class="cover-partners">
    <div class="partner"><span class="dot"></span>Pell Creek<br>First Nation</div>
    <div class="divider"></div>
    <div class="partner"><span class="dot"></span>Volu<br>Experiences</div>
  </div>
</section>

<!-- Invitation -->
<section class="page inner p-invite">
  <svg class="wave" style="left:0;top:0" width="280" height="40" viewBox="0 0 280 40" aria-hidden="true">
    <path d="M0 36 C25 20 60 16 80 20 C60 12 30 10 0 20Z" fill="var(--navy)"/>
    <path d="M65 28 C110 32 140 18 160 0 L140 0 C120 18 95 26 65 28Z" fill="var(--blue)"/>
  </svg>
  <div class="brand"><span class="dot"></span>Volu</div>
  <svg class="wave" style="left:250px;top:72px" width="30" height="40" viewBox="0 0 30 40" aria-hidden="true"><path d="M0 28 C12 22 22 14 30 2 L30 22 C22 30 12 32 0 28Z" fill="var(--blue)"/></svg>
  <div class="invite-body">
    <div class="float-spacer"></div>
    <div class="invite-photo" role="img" aria-label="Sunset over a green prairie meadow"></div>
    <p>Join us for an immersive cultural experience at Pell Creek First Nation (PCFN) community, located in Northeastern BC.</p>
    <p>We invite you to participate in the Volu Camping Experience, a unique opportunity to forge relationships with our community, connect with our Chief and Council, and engage with industry leaders. Your participation in this grassroots event will earn your company credibility for the work it performs in PCFN territory. You'll gain an appreciation and understanding of our community and cultural values, while meeting key office staff, industry C-Suite level executives, Indigenous relations staff, and local, regional and provincial representatives.</p>
    <p>The recent Tanwick V. British Columbia 2021 decision has significantly shifted how consultation and engagement will be managed on our lands. To help you better understand why managing cumulative effects is essential to PCFN, we welcome you to join us for a three-day camping experience from May 23 to May 26, 2023.</p>
    <p>The Volu Camping Experience offers a dinner visit to NAH 'B'lo, the 12,500-year-old cave, where an archeological dig is currently underway, accompanied by our economic development corporation team from Faret Development LP. The event also includes traditional bush camping in elegant teepees/wall tents, dry meat making, and participation in our Pell Day, a 30+ year cultural education and anti-racism event.</p>
    <p>Pell Day is held on May 25, 2023 and welcomes over 400+ students from School District #47 to participate in traditional activities including moose hide preparation, beaver skinning, archaeology dig, dry-meat making, trapping demonstrations, Bannock on a stick, storytelling, drumming, and tea dance around the campfire to the beat of our drums.</p>
    <p>Root yourself to the land, connect with your inner self, and be transformed alongside other important dignitaries as you partake in these multi-sensory experiences on our cultural grounds. This is our second combined camping/Pell Day experience, and we hope to build on it for future cultural tourism such as guided bush camps, hikes and hunts.</p>
    <p>If you are unable to join the full three-day camping experience, join us for the one-day Pell Day event. We have a helicopter landing area close to the activities. Please RSVP to Owen Marsh, Nahm? B'lo Cultural Productions Manager at OwenMarsh@pellcreekfn.example or Dale Finch, PCFN Councilor at Dfinch@pellcreekfn.example.</p>
  </div>
  <div class="signoff">WE LOOK FORWARD TO HOSTING YOU!</div>
</section>

<!-- Signatures -->
<section class="page inner p-sign">
  <svg class="wave" style="left:0;top:0" width="280" height="40" viewBox="0 0 280 40" aria-hidden="true">
    <path d="M0 36 C25 20 60 16 80 20 C60 12 30 10 0 20Z" fill="var(--navy)"/>
    <path d="M65 28 C110 32 140 18 160 0 L140 0 C120 18 95 26 65 28Z" fill="var(--blue)"/>
  </svg>
  <div class="brand"><span class="dot"></span>Volu</div>
  <h2 class="tab">Signature</h2>
  <ul class="sig-list">
    <li>Ross Tamlin, Chief PCFN<span class="rule"></span></li>
    <li>Dale Finch, PCFN Councilor<span class="rule"></span></li>
    <li>Carla Wendt, PCFN Councilor<span class="rule"></span></li>
    <li>Jolene Ashby, PCFN Councilor<span class="rule"></span></li>
  </ul>
  <div class="photo sign-photo" role="img" aria-label="Starry purple night sky over a snow-capped peak and spruce forest"></div>
  <svg class="wave" style="left:0;top:124px" width="280" height="50" viewBox="0 0 280 50" aria-hidden="true">
    <path d="M0 0 L280 0 L280 12 C240 2 200 4 170 14 C130 28 80 30 40 28 C25 27 10 22 0 15Z" fill="#fff"/>
    <path d="M0 15 C10 24 25 32 45 38 C25 36 10 30 0 24Z" fill="var(--navy)"/>
    <path d="M250 4 C262 6 272 10 280 14 L280 6 C270 4 260 3 250 4Z" fill="var(--blue)"/>
  </svg>
</section>

<!-- Sponsors -->
<section class="page inner p-sponsors">
  <svg class="wave" style="left:0;top:0" width="280" height="40" viewBox="0 0 280 40" aria-hidden="true">
    <path d="M0 36 C25 20 60 16 80 20 C60 12 30 10 0 20Z" fill="var(--navy)"/>
    <path d="M65 28 C110 32 140 18 160 0 L140 0 C120 18 95 26 65 28Z" fill="var(--blue)"/>
  </svg>
  <div class="brand"><span class="dot"></span>Volu</div>
  <h2 class="tab">2023 Sponsers</h2>
  <div class="sponsor-grid">
    <div class="sponsor"><span class="dot"></span>Vantor Energy</div>
    <div class="sponsor">Halden Energy</div>
    <div class="sponsor">Orbit Works</div>
    <div class="sponsor"><span class="dot"></span>Northland<br>Resource Board</div>
    <div class="sponsor">Kestrel</div>
    <div class="sponsor">Brightwell</div>
    <div class="sponsor">Ridgeline<br>Resources</div>
    <div class="sponsor"><span class="dot"></span>Astera</div>
    <div class="sponsor">Caldera</div>
    <div class="sponsor">Summit Works</div>
    <div class="sponsor">Groundline</div>
    <div class="sponsor"><span class="dot"></span>Faret Contracting</div>
    <div class="sponsor">Basin Exploration</div>
    <div class="sponsor">Keystone<br>Well Servicing</div>
    <div class="sponsor"><span class="dot"></span>Volu</div>
    <div class="sponsor"><span class="dot"></span>Pell Creek FN</div>
  </div>
  <svg class="wave" style="left:150px;top:176px" width="130" height="40" viewBox="0 0 130 40" aria-hidden="true">
    <path d="M0 40 C15 20 35 8 60 10 C40 14 22 26 14 40Z" fill="var(--blue)"/>
    <path d="M50 30 C80 32 110 20 130 6 L130 18 C110 28 80 34 50 30Z" fill="var(--navy)"/>
  </svg>
</section>

<!-- Checklist -->
<section class="page inner p-checklist">
  <svg class="wave" style="left:0;top:0" width="280" height="40" viewBox="0 0 280 40" aria-hidden="true">
    <path d="M0 36 C25 20 60 16 80 20 C60 12 30 10 0 20Z" fill="var(--navy)"/>
    <path d="M65 28 C110 32 140 18 160 0 L140 0 C120 18 95 26 65 28Z" fill="var(--blue)"/>
  </svg>
  <div class="brand"><span class="dot"></span>Volu</div>
  <h2 class="tab">Participant Supplies Checklist</h2>
  <p class="check-intro">We will be outside regardless of the weather so dress accordingly. If you do not have gear or clothes from this checklist then please let us know and we will outfit you to ensure you are comfortable and warm. You will be outside by the fire at night.<br><b>Average local temp for May is + 16 to + 4</b></p>
  <table class="supplies t-own">
    <tr><th>Item</th><th class="have">Have</th><th class="need">Need</th><th>Notes</th></tr>
    <tr><td>Pillow</td><td></td><td></td><td></td></tr>
    <tr><td>Personal medication</td><td></td><td></td><td></td></tr>
    <tr><td>Allergy medication (if applic)</td><td></td><td></td><td></td></tr>
    <tr><td>Own tent if preferred or you snore obnoxiously</td><td></td><td></td><td>We will have a few spare tents/tipis</td></tr>
    <tr><td>Warm weather top</td><td></td><td></td><td></td></tr>
    <tr><td>Spring weather jacket</td><td></td><td></td><td></td></tr>
    <tr><td>Spring weather base layers</td><td></td><td></td><td></td></tr>
    <tr><td>Rain shell (check weather)</td><td></td><td></td><td></td></tr>
    <tr><td>Hat &amp; mitts/gloves</td><td></td><td></td><td></td></tr>
    <tr><td>Sunscreen</td><td></td><td></td><td></td></tr>
    <tr><td>Pocket knife (checked luggage)</td><td></td><td></td><td>We will supply if you don't have one</td></tr>
    <tr><td>4 pairs wool or polyester socks</td><td></td><td></td><td></td></tr>
    <tr><td>Camp shoes</td><td></td><td></td><td></td></tr>
    <tr><td>Light hiking shoes/ rubber boots</td><td></td><td></td><td>Mountain boots not required this experience</td></tr>
    <tr><td>Flashlight</td><td></td><td></td><td></td></tr>
    <tr><td>Water bottle</td><td></td><td></td><td></td></tr>
    <tr><td>Coffee cup</td><td></td><td></td><td>Not required but preferred</td></tr>
  </table>
  <table class="supplies t-given">
    <tr class="group"><td colspan="4">Pell Creek Supplied</td></tr>
    <tr><td>Tipi/wall tent for sleeping</td><td class="mark">x</td><td></td><td>Wood stove provided for some tents</td></tr>
    <tr><td>Cot</td><td class="mark">x</td><td></td><td></td></tr>
    <tr><td>Insulated sleeping pad</td><td class="mark">x</td><td></td><td></td></tr>
    <tr class="group"><td colspan="4">Vantor Energy Supplied</td></tr>
    <tr><td>Sleeping bags</td><td class="mark">x</td><td></td><td>Please let us know if you are a larger person 280+ lbs or 6'5"+</td></tr>
  </table>
  <p class="check-foot">Print this out and do your own gear bag checklist. <span class="warn">As always bags can be more prepared, this is not a comprehensive list.</span><br>Please contact Owen Marsh asap if you need assistance at anytime. Email is best, text, then call.<br><span class="contact">owenmarsh@pellcreekfn.example 250-555-0147</span></p>
  <svg class="wave" style="left:200px;top:190px" width="80" height="26" viewBox="0 0 80 26" aria-hidden="true">
    <path d="M0 26 C10 12 25 6 40 8 C25 12 14 18 8 26Z" fill="var(--blue)"/>
    <path d="M40 20 C55 20 70 14 80 6 L80 14 C70 20 55 22 40 20Z" fill="var(--navy)"/>
  </svg>
</section>

<!-- Agenda -->
<section class="page inner p-agenda">
  <div class="photo agenda-photo" role="img" aria-label="Campfire at night beside a tipi with a person seated in a camp chair"></div>
  <svg class="wave" style="left:200px;top:0" width="40" height="216" viewBox="0 0 40 216" aria-hidden="true">
    <path d="M0 0 L12 0 C-4 50 0 90 20 130 C34 160 30 190 16 216 L0 216Z" fill="#fff"/>
    <path d="M12 0 L18 0 C4 30 2 60 8 80 C0 55 2 25 12 0Z" fill="var(--blue)"/>
    <path d="M16 216 C28 195 32 175 26 155 C34 178 32 200 22 216Z" fill="var(--navy)"/>
  </svg>
  <svg class="wave" style="left:0;top:0" width="200" height="40" viewBox="0 0 200 40" aria-hidden="true">
    <path d="M0 36 C25 20 60 16 80 20 C60 12 30 10 0 20Z" fill="var(--navy)"/>
    <path d="M65 28 C110 32 140 18 160 0 L140 0 C120 18 95 26 65 28Z" fill="var(--blue)"/>
  </svg>
  <h2 class="tab">Pell Creek Volu Executive Experience</h2>
  <div class="agenda-dates">MAY 23-26TH 2023</div>

  <table class="day d1">
    <tr><th class="c1">Day</th><th class="c2">Time</th><th class="c3">Activity</th><th>Details/Notes</th></tr>
    <tr><td>Tues, May 23</td><td>3:35 p.m.<br>4:00 p.m.<br>6:00 p.m.<br><br>6:00 p.m.</td><td>Flight arrives fr Calgary<br>Depart for NAH 'B'lo<br>Complete NAH 'B'lo tour<br>Dinner with Wade Rollins &amp; Jason Dale<br>Overnight in FSJ one night</td><td class="notes"><span class="flight">Northair NA8453</span><br><br>Lodgeway Inn room block under Vantor Energy. Please call and reserve min 24 hours before</td></tr>
  </table>
  <table class="day d2">
    <tr><th class="c1">Day</th><th class="c2">Time</th><th class="c3">Activity</th><th>Details/Notes</th></tr>
    <tr><td>Wed, May 24</td><td>3:35 p.m.<br>4:00 p.m.<br>6:00 p.m.<br><br>6:00 p.m.</td><td>Flight arrives fr Calgary<br>Depart for NAH 'B'lo<br>Complete NAH 'B'lo tour<br>Dinner with Wade Rollins &amp; Jason Dale<br>Overnight in FSJ one night</td><td class="notes"><span class="flight">Northair NA8453</span><br><br>Lodgeway Inn room block under Vantor Energy. Please call and reserve min 24 hours before</td></tr>
  </table>
  <table class="day d3">
    <tr><th class="c1">Day</th><th class="c2">Time</th><th class="c3">Activity</th><th>Details/Notes</th></tr>
    <tr><td>Thurs, May 25</td><td>3:35 p.m.<br>4:00 p.m.<br>6:00 p.m.<br><br>6:00 p.m.</td><td>Flight arrives fr Calgary<br>Depart for NAH 'B'lo<br>Complete NAH 'B'lo tour<br>Dinner with Wade Rollins &amp; Jason Dale<br>Overnight in FSJ one night</td><td class="notes"><span class="flight">Northair NA8453</span><br><br>Lodgeway Inn room block under Vantor Energy. Please call and reserve min 24 hours before</td></tr>
  </table>
  <table class="day d4">
    <tr><th class="c1">Day</th><th class="c2">Time</th><th class="c3">Activity</th><th>Details/Notes</th></tr>
    <tr><td>Fri, May 26</td><td>3:35 p.m.<br>4:00 p.m.<br>6:00 p.m.<br><br>6:00 p.m.</td><td>Flight arrives fr Calgary<br>Depart for NAH 'B'lo<br>Complete NAH 'B'lo tour<br>Dinner with Wade Rollins &amp; Jason Dale<br>Overnight in FSJ one night</td><td class="notes"><span class="flight">Northair NA8453</span><br><br>Lodgeway Inn room block under Vantor Energy. Please call and reserve min 24 hours before</td></tr>
  </table>
</section>

<!-- Thank you -->
<section class="page inner p-thanks">
  <div class="photo thanks-photo" role="img" aria-label="Large group of students seated on the grass around a central fire circle at the cultural grounds"></div>
  <svg class="wave" style="left:0;top:100px" width="280" height="70" viewBox="0 0 280 70" aria-hidden="true">
    <path d="M0 70 L0 40 C40 10 90 0 140 12 C190 24 230 50 280 40 L280 70Z" fill="#fff"/>
    <path d="M0 40 C40 8 90 -2 140 10 C95 4 45 14 0 48Z" fill="var(--navy)"/>
    <path d="M220 46 C245 50 265 42 280 30 L280 38 C262 48 242 52 220 46Z" fill="var(--blue)"/>
  </svg>
  <div class="thanks-text">
    <div class="pre">WE CAN'T WAIT TO SEE YOU THERE</div>
    <div class="greet">Wuujo aasanaláá</div>
    <div class="thanks">Thank You!</div>
  </div>
  <div class="brand-lg"><span class="dot"></span>Volu</div>
</section>

</body>
</html>
```